Business Card: RW Office Partners - Your organised problem solver

Business Name: RW Office Partners
Website: www.rwofficepartners.com.au
Email: marisol@rwofficepartners.com.au
Mobile: 61 482 907 236
Facebook: @rwofficepartners
Instrgram: @rwofficepartners

Brading Colours:
HEX
#986474
#ddccd3
#7a8498
#c9d8e4
#000000
#ffffff

Tag Line: Your organised problem solver

Link to DRAFT website:
https://deskhelpcollective.wixsite.com/rw-office-partners

About Page from the website:
My name is Marisol Wrenfield, and I would love to assist you to become more productive in your day to day and achieve your business and personal goals.
My mission is to give you time, time to work on the important tasks of your business or to be able to spend more time with your family. I will take on the tasks you don’t have time for, don’t know well or simply don’t like to do.
I have an extensive background in Administration, Tender Coordination, Document Control, WHS and Quality Management working primarily in the Construction, Mining and Corporate World.
I am passionate about being organised, having order and making things in your life (and mine) easier! I love to watch something unfold and grow into something amazing! I am known for being the go-to problem solver, the organiser of all things, producing high standards of work even under pressure. I’m also a confident communicator, and I understand that you’re busy running your business.

Target Market(s)

Small to Medium Business who require assistance in their business by a virtual assistant.

Industry/Entity Type

Virtual Assistant

Contact Information for Business Card

Mobile: 61 482 907 236

Font styles to use
Sans Serif

Colors
ffffff

Requirements
Must have
• Branding Colours as outlined.
Contact Details as outlined.
Logo as provided.
Proper contact details - mobile, facebook, instragm, website.
Simple, Elegant, very clean looking.
Should not have
• Note cute with pictures.
Not too girly as still want to market to construction companies.

```html
<!DOCTYPE html>
<html lang="en">
<head>
<meta charset="utf-8">
<title>RW Office Partners – Business Card</title>
<link rel="stylesheet" href="https://fonts.googleapis.com/css2?family=Montserrat:wght@500;600;700&family=Roboto:wght@400&display=swap">
<style>
  :root {
    --mauve: #8b5f6e;
    --mauve-light: #986474;
    --slate: #7a8498;
    --white: #ffffff;
    --paper: #fbfbfb;
    --backdrop: #6e6a6b;
  }
  * { margin: 0; padding: 0; box-sizing: border-box; }
  html, body { width: 1200px; height: 1200px; overflow: hidden; }
  body {
    background: var(--backdrop);
    position: relative;
    font-family: "Roboto", Arial, sans-serif;
  }
  .card {
    position: absolute;
    left: 238px;
    width: 712px;
    height: 420px;
    border-radius: 24px;
    overflow: hidden;
  }
  .card-front { top: 118px; background: var(--mauve); }
  .card-back { top: 643px; }
  .card-back .card-shapes { position: absolute; inset: 0; }

  .front-wordmark {
    position: absolute;
    inset: 0;
    display: flex;
    align-items: center;
    justify-content: center;
    font-family: "Montserrat", Arial, sans-serif;
    font-weight: 600;
    font-size: 46px;
    color: var(--white);
    letter-spacing: 0.5px;
  }

  .back-wordmark {
    position: absolute;
    left: 20px;
    top: 130px;
    width: 230px;
    text-align: center;
    font-family: "Montserrat", Arial, sans-serif;
    font-weight: 600;
    font-size: 34px;
    line-height: 1.15;
    color: var(--mauve);
  }

  .contact-block {
    position: absolute;
    left: 342px;
    top: 88px;
    color: var(--white);
  }
  .person-name {
    font-family: "Montserrat", Arial, sans-serif;
    font-weight: 700;
    font-size: 25px;
  }
  .person-role {
    font-size: 17px;
    margin-top: 4px;
  }
  .contact-list {
    list-style: none;
    margin-top: 28px;
  }
  .contact-list li {
    display: flex;
    align-items: center;
    font-size: 17.5px;
    height: 26.5px;
  }
  .contact-icon {
    width: 16px;
    height: 16px;
    margin-right: 14px;
    flex-shrink: 0;
  }
  .tagline {
    position: absolute;
    left: 342px;
    top: 347px;
    font-size: 17.5px;
    color: var(--white);
  }
</style>
</head>
<body>
  <section class="card card-front">
    <div class="front-wordmark">RW Office Partners</div>
  </section>

  <section class="card card-back">
    <svg class="card-shapes" viewBox="0 0 712 420" width="712" height="420">
      <rect width="712" height="420" fill="var(--mauve)"/>
      <rect x="200" y="343" width="512" height="32" fill="var(--slate)"/>
      <path d="M0 0 H264 Q360 210 264 420 H0 Z" fill="var(--slate)"/>
      <path d="M0 0 H252 Q346 210 252 420 H0 Z" fill="var(--paper)"/>
    </svg>

    <div class="back-wordmark">RW Office<br>Partners</div>

    <div class="contact-block">
      <div class="person-name">Marisol Wrenfield</div>
      <div class="person-role">Virtual Assistant</div>
      <ul class="contact-list">
        <li>
          <svg class="contact-icon" viewBox="0 0 16 16"><path d="M3 2 L6 2 L7 5 L5.5 6.5 Q7 9.5 9.5 10.5 L11 9 L14 10 L14 13 Q8 14 4.5 10 Q2 7 3 2 Z" fill="var(--white)"/></svg>
          61 482 907 236
        </li>
        <li>
          <svg class="contact-icon" viewBox="0 0 16 16"><rect x="1.5" y="3.5" width="13" height="9" fill="none" stroke="var(--white)" stroke-width="1.5"/><path d="M1.5 3.5 L8 9 L14.5 3.5" fill="none" stroke="var(--white)" stroke-width="1.5"/></svg>
          marisol@rwofficepartners.com.au
        </li>
        <li>
          <svg class="contact-icon" viewBox="0 0 16 16"><circle cx="8" cy="8" r="6.5" fill="none" stroke="var(--white)" stroke-width="1.2"/><ellipse cx="8" cy="8" rx="3" ry="6.5" fill="none" stroke="var(--white)" stroke-width="1.2"/><path d="M1.5 8 H14.5" stroke="var(--white)" stroke-width="1.2"/></svg>
          www.rwofficepartners.com.au
        </li>
        <li>
          <svg class="contact-icon" viewBox="0 0 16 16"><rect x="1.5" y="1.5" width="13" height="13" rx="2" fill="var(--white)"/></svg>
          @rwofficepartners
        </li>
        <li>
          <svg class="contact-icon" viewBox="0 0 16 16"><circle cx="8" cy="8" r="6.5" fill="none" stroke="var(--white)" stroke-width="1.5"/></svg>
          @rwofficepartners
        </li>
      </ul>
    </div>

    <div class="tagline">Your organised problem solver</div>
  </section>
</body>
</html>
```